Shipping and Logistics, Project

Project description : Company Profile

A total logistics company covering domestic / international freight forwarding, warehouse management services, haulage, supply chain management, transport management & distribution, procurement & assembly services, shipping, chartering & bunker services, project logistics & tax exemption consultancy, oil & gas logistics, halal logistics services & integrated logistics management. We’re a well-established and experienced freight forwarder in Kuala Lumpur, Malaysia. We specialize in customized value-added solution that optimizes your supply chain by trimming inventory, reducing logistics cost and enhancing your customer service levels.

As a member of the Worldwide Parcel and Carriage Alliance which comprise of 170 global freight agents in 80 countries that promotes great handling in cross-trade logistics and freighting. You could rely on our efficiency in handlings of export cargo (FCL, LCL, Bulk and Conventional) between our global network offices worldwide with a total scale of 10,000 groomed specialists in various logistics division working together to ensure delivery task meets with your expectation. With our dedicated qualified and experienced professionals, we are fully committed to serving our clients.

Our generic services are listed below for your reference:

• Air Freight
• Ocean Freight FCL & LCL
• Container Haulage
• Warehousing
• Transportation and Distribution within Malaysia and Thailand
• Cross-Border Road Line-hauls between Thailand, Malaysia, Singapore and Laos
• Customs Brokerage and Forwarding
• Project Cargo Freight Forwarding for setting up of new plants / factories and ad hoc heavy-lift
• Air-Sea-Road-Rail multi-modal options
• Import / Export / Storage / Documentation / Handling of DG / Hazmat
• Vessel and Aircraft Charters

Our Mission
Based on the motto “Quick, Reliable and Polite”, we are dedicated to upholding the following three points corporate philosophy:
1. Adhering to the principle that “the customer always comes first”.
2. Contributing to the development of the local community.
3. Making it our duty to be responsible and sincere.

Our Edge
• One-Stop Logistics Solutions
• Extensive Network Throughout Malaysia
• Highly Qualified and Experienced Pool of Professionals
• Comprehensive IT Solutions
• Innovative and Customer-focused Solutions
• Flexible and Consistent in Managing Exceptions
• Total Supply Chain Visibility

Target Market
1. We sell the logistics services to all the industry in Malaysia and Worldwide. (ONE Stop Logistics Solutions)

Competitor
1. TR Valmont
2. Corvessa Transport
3. Brandt + Loewe
4. FELRO
5. QTV
6. Routemarks
7. Ilto Logistics

Rules for Picking a Company Name
1. Unique and unforgettable
2. Avoid unusual spellings
3. Easy to pronounce and remember
4. Keep it simple
5. Make some sense
6. Give a clue

Rules for Picking a Company Logo
4. Keep it simple
5. Make some sense
6. Give a clue

1. Simplicity
2. Memorability
3. Originality
4. Modern Yet Timeless
5. Balance
6. Complementary
7. Versatility

Stationery Information
1. Company Name : ZENFreight Solutions Sdn Bhd
2. Company Registration : 2837165-W
3. Address : 42-08, Jalan Cempaka Indah 5, Taman Seri Bayu, 81300 Johor Bahru, Johor, Malaysia.
4. Name : Derek Tan
5. Position : Manager
6. Mobile No : (+6019) 4381907
7. Office No : (+607) 5218764
8. Fax No : Not Available
9. Email Address : derek.tan@zenfreight-solutions.example
10. Web Domain : www.zenfreight-solutions.example
11. Company Slogan : Be Globally Connected

Target Market(s)

Corporate Company

Industry/Entity Type

Shipping and Logistics Industry

Requirements
Must have
• Company Full Name : ZENFREIGHT SOLUTIONS SDN. BHD.
Nice to have
• Keep it simple and unforgettable ...

```html
<!DOCTYPE html>
<html lang="en">
<head>
<meta charset="utf-8">
<title>ZENFreight Solutions – Business Card</title>
<link href="https://fonts.googleapis.com/css2?family=Montserrat:wght@500;600;700&family=Open+Sans:wght@400;600&display=swap" rel="stylesheet">
<style>
  :root {
    --backdrop: #1b1b1b;
    --card-dark: #262626;
    --card-light: #ffffff;
    --brand-blue: #2f86d9;
    --ink: #1a1a1a;
    --white: #ffffff;
  }
  * { margin: 0; padding: 0; box-sizing: border-box; }
  html, body { width: 1200px; height: 1015px; overflow: hidden; }
  body { background: var(--backdrop); position: relative; }

  .card {
    position: absolute;
    left: 220px;
    width: 760px;
    height: 434px;
    overflow: hidden;
  }

  /* ---------- back side ---------- */
  .card--back { top: 50px; background: var(--card-dark); font-family: "Montserrat", sans-serif; }
  .registration {
    position: absolute; top: 62px; width: 100%; text-align: center;
    color: var(--white); font-size: 17px; font-weight: 500; letter-spacing: 0.5px;
  }
  .registration .registration-number { color: var(--brand-blue); }
  .brand-lockup {
    position: absolute; top: 150px; left: 0; width: 100%;
    display: flex; justify-content: center; align-items: center; gap: 26px;
  }
  .brand-square { width: 92px; height: 92px; border: 9px solid var(--brand-blue); }
  .brand-name { color: var(--white); font-size: 50px; font-weight: 700; letter-spacing: 2px; line-height: 1; }
  .brand-entity { color: var(--white); font-size: 16px; font-weight: 700; letter-spacing: 4.5px; margin-top: 10px; }
  .tagline {
    position: absolute; bottom: 62px; width: 100%; text-align: center;
    color: var(--brand-blue); font-size: 19px; font-weight: 600; letter-spacing: 1.5px;
  }

  /* ---------- front side ---------- */
  .card--front { top: 534px; background: var(--card-light); font-family: "Open Sans", sans-serif; color: var(--ink); }
  .brand-decoration { position: absolute; left: 440px; top: 40px; }
  .holder { position: absolute; left: 58px; top: 150px; }
  .holder-name { font-family: "Montserrat", sans-serif; font-size: 34px; font-weight: 700; letter-spacing: 1px; line-height: 1; }
  .holder-name .surname { color: var(--brand-blue); }
  .holder-role { font-size: 17px; margin-top: 4px; }
  .address { position: absolute; left: 58px; top: 228px; font-size: 17px; line-height: 23px; font-style: normal; }
  .contacts { position: absolute; left: 58px; top: 340px; list-style: none; font-size: 17px; line-height: 22px; }
  .contacts li { display: flex; align-items: center; gap: 8px; }
  .contacts svg { width: 16px; height: 16px; flex: none; }
  .contacts .accent { color: var(--brand-blue); }
</style>
</head>
<body>

  <section class="card card--back" aria-label="Card back">
    <p class="registration">Registration : <span class="registration-number">2837165-W</span></p>
    <div class="brand-lockup">
      <div class="brand-square"></div>
      <div>
        <div class="brand-name">ZENFREIGHT</div>
        <div class="brand-entity">SOLUTIONS SDN. BHD.</div>
      </div>
    </div>
    <p class="tagline">BE GLOBALLY CONNECTED</p>
  </section>

  <section class="card card--front" aria-label="Card front">
    <svg class="brand-decoration" width="300" height="300" viewBox="0 0 300 300" aria-hidden="true">
      <rect x="14" y="14" width="272" height="272" fill="none" stroke="var(--brand-blue)" stroke-width="22"/>
    </svg>

    <div class="holder">
      <h1 class="holder-name">DEREK <span class="surname">TAN</span></h1>
      <p class="holder-role">Manager</p>
    </div>

    <address class="address">
      42-08, Jalan Cempaka Indah 5<br>
      Taman Seri Bayu<br>
      81300 Johor Bahru<br>
      Johor, Malaysia
    </address>

    <ul class="contacts">
      <li>
        <svg viewBox="0 0 16 16" aria-hidden="true"><rect x="4" y="1" width="8" height="14" rx="1.5" fill="none" stroke="var(--brand-blue)" stroke-width="1.6"/><circle cx="8" cy="12.3" r="0.9" fill="var(--brand-blue)"/></svg>
        (+6019) 4381907
      </li>
      <li>
        <svg viewBox="0 0 16 16" aria-hidden="true"><path d="M3 2l3 0 1 3.5-1.8 1.2a9 9 0 0 0 4.1 4.1L10.5 9 14 10v3a1.5 1.5 0 0 1-1.6 1.5A12 12 0 0 1 1.5 3.6 1.5 1.5 0 0 1 3 2z" fill="var(--brand-blue)"/></svg>
        (+607) 5218764
      </li>
      <li>
        <svg viewBox="0 0 16 16" aria-hidden="true"><rect x="1" y="3" width="14" height="10" fill="var(--brand-blue)"/><path d="M1 3l7 6 7-6" fill="none" stroke="#fff" stroke-width="1.2"/></svg>
        derek.tan@zenfreight-solutions.example
      </li>
      <li>
        <svg viewBox="0 0 16 16" aria-hidden="true"><g fill="none" stroke="var(--brand-blue)" stroke-width="1.3"><circle cx="8" cy="8" r="6.5"/><ellipse cx="8" cy="8" rx="3" ry="6.5"/><path d="M1.5 8h13M2.5 4.8h11M2.5 11.2h11"/></g></svg>
        <span>www.<span class="accent">zenfreight-solutions</span>.example</span>
      </li>
    </ul>
  </section>

</body>
</html>
```